real esate business card with company logo and name

we need a business card design for a real esate company

The company name is Walsh & Brand Pty Ltd, and we have our logo designed and will upload. We want classic or moden feel. Black or white background. looks more textured. Should include folowinginformations
Owen Walsh and Lucy Brand
Sales Agents & Onsite Manager
p: 07 5948 2063
F: 07 5948 2174
M:0431 857 219
3/42 Marlow Crescent, FERNLEA QLD 4213

We want this business card looks professonal. Thank you in advance.

Industry/Entity Type

Real Estate Agent

Contact Information for Business Card

Owen Walsh and Lucy Brand
Onsite Manager & Sales Agents
p: 07 5948 2063
M:0431 857 219

Font styles to use
Serif

Colors
000000
fbfbfb
333333
959595

Requirements
Must have
• company logo and name, black or white back ground

```html
<!DOCTYPE html>
<html lang="en">
<head>
<meta charset="utf-8">
<title>Walsh &amp; Brand Pty Ltd — Business Card</title>
<link rel="stylesheet" href="https://fonts.googleapis.com/css2?family=Open+Sans:wght@400;600&family=Oswald:wght@300;400&display=swap">
<style>
  :root {
    --page-bg: #ececec;
    --card-white: #ffffff;
    --panel-light: #c1c1c1;
    --panel-dark: #4f5052;
    --divider: #ffffff;
    --ink-dark: #333333;
    --ink-mid: #3f3f3f;
    --ink-brand: #959595;
    --mark-grey: #7a7a7a;
  }
  * { margin: 0; padding: 0; box-sizing: border-box; }
  html, body {
    width: 1200px;
    height: 900px;
    overflow: hidden;
    background: var(--page-bg);
    font-family: "Open Sans", Arial, sans-serif;
  }
  .canvas {
    position: relative;
    width: 1200px;
    height: 900px;
  }

  /* Front of card */
  .card-front {
    position: absolute;
    left: 238px;
    top: 62px;
    width: 555px;
    height: 342px;
    overflow: hidden;
    box-shadow: 0 4px 14px rgba(0,0,0,0.18);
  }
  .card-front__panels {
    position: absolute;
    inset: 0;
    width: 100%;
    height: 100%;
  }
  .card-front__names {
    position: absolute;
    left: 41px;
    top: 34px;
    font-size: 19px;
    font-weight: 600;
    color: var(--ink-mid);
    letter-spacing: 0.1px;
  }
  .card-front__role {
    position: absolute;
    left: 41px;
    top: 62px;
    font-size: 14.5px;
    color: var(--ink-mid);
  }
  .card-front__address {
    position: absolute;
    left: 41px;
    top: 120px;
    font-size: 13.5px;
    line-height: 18px;
    color: var(--ink-dark);
  }
  .card-front__contacts {
    position: absolute;
    left: 41px;
    top: 173px;
    list-style: none;
    font-size: 14px;
    line-height: 21px;
    color: var(--ink-dark);
  }
  .contact-line {
    display: flex;
    align-items: center;
    gap: 9px;
  }
  .contact-line svg { width: 12px; height: 12px; fill: var(--ink-dark); }
  .card-front__brand {
    position: absolute;
    left: 318px;
    top: 206px;
    display: flex;
    align-items: center;
    gap: 10px;
    font-size: 17px;
    font-weight: 600;
    color: var(--card-white);
    white-space: nowrap;
  }
  .brand-square {
    width: 16px;
    height: 16px;
    background: var(--card-white);
  }

  /* Back of card */
  .card-back {
    position: absolute;
    left: 457px;
    top: 518px;
    width: 560px;
    height: 343px;
    background: var(--card-white);
    box-shadow: 0 4px 14px rgba(0,0,0,0.15);
  }
  .card-back__square {
    position: absolute;
    left: 228px;
    top: 96px;
    width: 104px;
    height: 104px;
    background: var(--mark-grey);
  }
  .card-back__company {
    position: absolute;
    left: 0;
    right: 0;
    top: 258px;
    text-align: center;
    font-family: "Oswald", "Arial Narrow", sans-serif;
    font-weight: 400;
    font-size: 27px;
    letter-spacing: 1px;
    color: var(--ink-brand);
    text-transform: uppercase;
  }
</style>
</head>
<body>
<main class="canvas">

  <section class="card-front" aria-label="Business card front">
    <svg class="card-front__panels" viewBox="0 0 555 342" preserveAspectRatio="none" aria-hidden="true">
      <rect width="555" height="342" fill="var(--panel-light)"/>
      <polygon points="555,0 555,342 0,342" fill="var(--panel-dark)"/>
      <line x1="555" y1="0" x2="0" y2="342" stroke="var(--divider)" stroke-width="3"/>
    </svg>

    <h1 class="card-front__names">Owen Walsh and Lucy Brand</h1>
    <p class="card-front__role">Onsite Manager &amp; Sales Agents</p>

    <address class="card-front__address">3/42 Marlow Crescent, FERNLEA<br>QLD 4213</address>

    <ul class="card-front__contacts">
      <li class="contact-line">
        <svg viewBox="0 0 12 12" aria-hidden="true"><rect x="3" y="0.5" width="6" height="11" rx="1"/><rect x="4" y="2" width="4" height="7" fill="var(--panel-light)"/></svg>
        07 5948 2063
      </li>
      <li class="contact-line">
        <svg viewBox="0 0 12 12" aria-hidden="true"><path d="M1 4 Q6 0 11 4 L10 5.5 L8 5 L8 4 Q6 3 4 4 L4 5 L2 5.5 Z"/><rect x="2" y="6" width="8" height="5" rx="1"/></svg>
        0431 857 219
      </li>
    </ul>

    <div class="card-front__brand">
      <span class="brand-square" aria-hidden="true"></span>
      Walsh &amp; Brand Pty Ltd
    </div>
  </section>

  <section class="card-back" aria-label="Business card back">
    <span class="card-back__square" aria-hidden="true"></span>
    <p class="card-back__company">Walsh &amp; Brand Pty Ltd.</p>
  </section>

</main>
</body>
</html>
```